Pinecrest Real Estate A5 Flyer

A5 Flyer for print distribution.

Front (include attached photo and branding):
Pinecrest are a new face in the Dunmore & Kelvinhurst real estate market. The Pinecrest team are both Dunmore ‘locals’ and are genuinely and sincerely committed to this community. They put people first and pursue exceptional outcomes for their clients. This is the founding vision of Pinecrest.

Values:
Outstanding Customer Service
Timely Communication
Integrity Always
People First
Exceptional Negotiation

If you’re thinking of selling, interested in a free market appraisal, or simply want to find out more about the Pinecrest team, please reach out to Trevor or Owen for a chat. We’d love to shout you a coffee at The Marigold Coffee + Kitchen.

Pinecrest Real Estate
E: hello@pinecrestrealestate-example.com.au
W: pinecrestrealestate-example.com.au

Back (half the page about Trevor, other half the page about Owen). Please include headshots (Owen is the younger one):

Owen Pritchard (Property Consultant):

Owen has an in-depth understanding of all things property & finance related. With a degree in property & finance, diploma in finance & mortgage broking, certificate IV in real estate practice, project management roles in residential property development, plus years of small business experience as co-founder/co-owner of The Marigold Coffee + Kitchen, his experience in managing competing demands and complex scenarios runs far and wide.

Owen also has experience in corporate negotiations which is proving to be a very beneficial skill set. Owen is deeply committed to people and pursuing exceptional outcomes for his clients. He has built a reputation as a man of his word who is genuine and sincere and willing to go above and beyond for his clients.

owen@pinecrestrealestate-example.com.au
0400 118 204

Trevor Bungey (Director / Licensee):

Trevor has worked in various roles inclusive of being a Real Estate Agent, Bank Manager, Financial Counsellor, Mortgage Broker, and previously a Commercial Pilot. He spent eight years in remote Western Australia, where he worked for an international mining company creating strategies to help support the well-being of employees. Trevor’s focus in life has always been to help people. To him, it is always about the relationship. Trevor gets enormous satisfaction from seeing individuals, families, and businesses thrive financially. He has become a skilled negotiator with extensive experience working for a number of corporations and private firms.
 
What differentiates Trevor is his compassion and commitment to people. He works hard to be an excellent communicator with the aim of achieving great results. He  has extensive sales experience with incredible ability to push the boundaries, think outside the box and meet or surpass expectations. This is why his clients keep coming back and continue to refer well into the future. 

trevor@pinecrestrealestate-example.com.au
0400 362 917

Target Market(s)

House Sellers / House Buyers

Industry/Entity Type

Real Estate

Colors
0054AA
0677BA
7BADD7
CADEEF
E8F1F8

Requirements
Must have
• Branding / logo, river photo, head shots, company details etc
Nice to have
• Design as per attached branding guide

```html
<!DOCTYPE html>
<html lang="en">
<head>
<meta charset="utf-8">
<title>Pinecrest Real Estate – Team Flyer</title>
<link href="https://fonts.googleapis.com/css2?family=Montserrat:wght@400;500;700;800&display=swap" rel="stylesheet">
<style>
  :root{
    --blue-deep:#0054AA;
    --blue-mid:#0677BA;
    --blue-soft:#7BADD7;
    --blue-pale:#CADEEF;
    --blue-wash:#E8F1F8;
    --navy:#0f1e2e;
    --ink:#1b1f24;
    --frame:#a9adb2;
    --white:#ffffff;
  }
  *{box-sizing:border-box;margin:0;padding:0}
  html,body{width:862px;height:1200px;overflow:hidden;background:var(--white)}
  body{font-family:"Montserrat",sans-serif;color:var(--ink);position:relative}

  .brand{position:absolute;left:155px;top:39px;display:flex;align-items:center;gap:20px}
  .brand-dot{width:83px;height:83px;border-radius:50%;background:var(--navy)}
  .brand-name{font-size:40px;font-weight:400;letter-spacing:12px;color:var(--navy)}

  .profile{position:absolute;left:52px;width:760px}
  .profile-card{position:absolute;left:0;right:0;bottom:0;border:2px solid var(--frame);border-radius:22px;overflow:hidden;background:var(--white)}
  .ribbon-tabs{position:absolute;top:0;left:47px;width:653px;height:24px;background:var(--blue-deep);border-radius:12px 12px 0 0}
  .ribbon{position:absolute;top:7px;left:80px;width:586px;height:47px;border-radius:0 0 24px 24px;
    background:linear-gradient(180deg,var(--blue-mid),var(--blue-deep));color:var(--white);
    display:flex;align-items:baseline;justify-content:center;gap:9px;padding-top:9px}
  .ribbon-name{font-size:25px;font-weight:800;letter-spacing:.2px}
  .ribbon-role{font-size:15px;font-weight:500}

  .bio{position:absolute;left:0;right:0;font-size:15.6px;line-height:22.2px;font-weight:400;z-index:2}
  .bio-line{display:block;white-space:nowrap;padding-left:var(--i,22px)}
  .bio-gap{display:block;height:22.2px}

  .contact-bar{position:absolute;bottom:0;height:49px;background:var(--navy);color:var(--white);
    display:flex;align-items:center;gap:8px;padding-left:14px}
  .contact-icon{width:22px;height:22px;flex:none}
  .contact-phone{font-size:16px;font-weight:700;margin-right:6px}
  .contact-email{font-size:15px;font-weight:500}

  .headshot{position:absolute;background:linear-gradient(180deg,var(--blue-wash) 0%,#c9d3dd 40%,#2d4263 70%,#1f2f4a 100%)}

  /* Owen */
  .profile--owen{top:152px;height:429px}
  .profile--owen .profile-card{top:19px}
  .profile--owen .bio{top:42px}
  .profile--owen .contact-bar{left:0;width:556px}
  .profile--owen .headshot{left:544px;top:108px;width:214px;height:302px;
    clip-path:polygon(75px 0,165px 0,175px 60px,170px 130px,214px 170px,214px 302px,0 302px,10px 250px,30px 205px,70px 175px,66px 120px,62px 60px)}

  /* Trevor */
  .profile--trevor{top:624px;height:493px}
  .profile--trevor .profile-card{top:19px}
  .profile--trevor .bio{top:48px}
  .profile--trevor .headshot{left:0;top:161px;width:222px;height:313px;
    clip-path:polygon(40px 0,125px 0,143px 60px,140px 130px,160px 150px,205px 175px,222px 230px,222px 313px,0 313px,0 160px,25px 140px,27px 60px)}
  .profile--trevor .contact-bar{right:0;width:536px}

  .web{position:absolute;left:0;right:0;top:1141px;text-align:center;font-size:23px;font-weight:800;color:var(--blue-mid)}
</style>
</head>
<body>

<header class="brand">
  <span class="brand-dot"></span>
  <span class="brand-name">PINECREST</span>
</header>

<section class="profile profile--owen">
  <div class="profile-card">
    <div class="contact-bar">
      <svg class="contact-icon" viewBox="0 0 22 22"><circle cx="11" cy="11" r="11" fill="var(--blue-soft)"/><path d="M7 6.5c.6-.6 1.3-.5 1.7.1l1 1.5c.3.5.2 1-.2 1.4l-.6.6c.5 1.2 1.5 2.2 2.7 2.7l.6-.6c.4-.4.9-.5 1.4-.2l1.5 1c.6.4.7 1.1.1 1.7l-.7.7c-.9.9-4 .3-6.3-2s-2.9-5.4-2-6.3z" fill="var(--white)"/></svg>
      <span class="contact-phone">0400 118 204</span>
      <svg class="contact-icon" viewBox="0 0 22 22"><circle cx="11" cy="11" r="11" fill="var(--blue-soft)"/><rect x="6" y="7.5" width="10" height="7" rx="1" fill="none" stroke="var(--white)" stroke-width="1.3"/><path d="M6.5 8.2 11 11.5l4.5-3.3" fill="none" stroke="var(--white)" stroke-width="1.3"/></svg>
      <span class="contact-email">owen@pinecrestrealestate-example.com.au</span>
    </div>
    <div class="headshot" role="img" aria-label="Headshot of Owen Pritchard, smiling, in a navy suit and light blue shirt"></div>
    <p class="bio">
      <span class="bio-line">Owen has an in-depth understanding of all things property &amp; finance related. With a</span>
      <span class="bio-line">degree in property &amp; finance, diploma in finance &amp; mortgage broking,</span>
      <span class="bio-line">certificate IV in real estate practice, project management roles in</span>
      <span class="bio-line">residential property development, plus years of small business</span>
      <span class="bio-line">experience as co-founder/co-owner of The Marigold Coffee + Kitchen, his</span>
      <span class="bio-line">experience in managing competing demands and complex scenarios</span>
      <span class="bio-line">runs far and wide.</span>
      <span class="bio-gap"></span>
      <span class="bio-line">Owen also has experience in corporate negotiations which is proving</span>
      <span class="bio-line">to be a very beneficial skill set. Owen is deeply committed to people</span>
      <span class="bio-line">and pursuing exceptional outcomes for his clients. He has built a</span>
      <span class="bio-line">reputation as a man of his word who is genuine and sincere</span>
      <span class="bio-line">and willing to go above and beyond for his clients.</span>
    </p>
  </div>
  <div class="ribbon-tabs"></div>
  <h2 class="ribbon"><span class="ribbon-name">OWEN PRITCHARD</span><span class="ribbon-role">PROPERTY CONSULTANT</span></h2>
</section>

<section class="profile profile--trevor">
  <div class="profile-card">
    <div class="headshot" role="img" aria-label="Headshot of Trevor Bungey in a navy suit with a striped tie"></div>
    <div class="contact-bar">
      <svg class="contact-icon" viewBox="0 0 22 22"><circle cx="11" cy="11" r="11" fill="var(--blue-soft)"/><path d="M7 6.5c.6-.6 1.3-.5 1.7.1l1 1.5c.3.5.2 1-.2 1.4l-.6.6c.5 1.2 1.5 2.2 2.7 2.7l.6-.6c.4-.4.9-.5 1.4-.2l1.5 1c.6.4.7 1.1.1 1.7l-.7.7c-.9.9-4 .3-6.3-2s-2.9-5.4-2-6.3z" fill="var(--white)"/></svg>
      <span class="contact-phone">0400 362 917</span>
      <svg class="contact-icon" viewBox="0 0 22 22"><circle cx="11" cy="11" r="11" fill="var(--blue-soft)"/><rect x="6" y="7.5" width="10" height="7" rx="1" fill="none" stroke="var(--white)" stroke-width="1.3"/><path d="M6.5 8.2 11 11.5l4.5-3.3" fill="none" stroke="var(--white)" stroke-width="1.3"/></svg>
      <span class="contact-email">trevor@pinecrestrealestate-example.com.au</span>
    </div>
    <p class="bio">
      <span class="bio-line">Trevor has worked in various roles inclusive of being a Real Estate Agent, Bank Manager,</span>
      <span class="bio-line">Financial Counsellor, Mortgage Broker, and previously a Commercial Pilot. He spent</span>
      <span class="bio-line">eight years in remote Western Australia, where he worked for an international mining</span>
      <span class="bio-line">company creating strategies to help support the well-being of employees. Trevor’s</span>
      <span class="bio-line" style="--i:123px">focus in life has always been to help people. To him, it is always about the</span>
      <span class="bio-line" style="--i:142px">relationship. Trevor gets enormous satisfaction from seeing individuals,</span>
      <span class="bio-line" style="--i:150px">families, and businesses thrive financially. He has become a skilled</span>
      <span class="bio-line" style="--i:158px">negotiator with extensive experience working for a number of</span>
      <span class="bio-line" style="--i:160px">corporations and private firms.</span>
      <span class="bio-gap"></span>
      <span class="bio-line" style="--i:147px">What differentiates Trevor is his compassion and commitment to people.</span>
      <span class="bio-line" style="--i:170px">He works hard to be an excellent communicator with the aim of</span>
      <span class="bio-line" style="--i:207px">achieving great results. He has extensive sales experience with</span>
      <span class="bio-line" style="--i:223px">incredible ability to push the boundaries, think outside the box</span>
      <span class="bio-line" style="--i:228px">and meet or surpass expectations. This is why his clients keep</span>
      <span class="bio-line" style="--i:232px">coming back and continue to refer well into the future.</span>
    </p>
  </div>
  <div class="ribbon-tabs"></div>
  <h2 class="ribbon"><span class="ribbon-name">TREVOR BUNGEY</span><span class="ribbon-role">DIRECTOR / LICENSEE</span></h2>
</section>

<footer class="web">www.pinecrestrealestate-example.com.au</footer>

</body>
</html>
```